Personal Web page for recruiter and owner of consulting firm

I work full time as a recruiter so I want a page that allows for me to support my efforts. I would like a long single page, I need to be able to upload four two minute videos, and 4 images. I also want the color scheme to match with my consulting company. I own the domain marcusfenwold.net already through wordpress . I took a shot at it myself and its terrible.

Target Market(s)

Potential clients

Industry/Entity Type

Management Consulting

Logo Text

marcus fenwold

Font styles to use
Serif

Requirements
Must have
• Must in color scheme go well with my consulting company logo attached
• Must be able to upload 4 two minute videos and 4 images (photos of me)
• Single long scroll page
• Modern and clean
Nice to have
• Easy for me to update videos images and text without complex coding
Should not have
• I want the design and feel to go well with my logos not exactly replicate it

```html
<!DOCTYPE html>
<html lang="en">
<head>
<meta charset="utf-8">
<title>Fenwold Strategies — Marcus Fenwold</title>
<link rel="stylesheet" href="https://fonts.googleapis.com/css2?family=Open+Sans:wght@400;600;700&family=Montserrat:wght@600;700&display=swap">
<style>
:root{
  --blue:#2f74b8;
  --blue-soft:#4f8fcc;
  --navy:#1b3557;
  --ink:#2c3440;
  --text:#6b7480;
  --line:#d9dee5;
  --dark:#1f2428;
  --white:#ffffff;
  --paper:#f6f8fa;
}
*{box-sizing:border-box;margin:0;padding:0}
html,body{width:1200px;height:4956px;overflow:hidden;background:var(--white)}
body{font-family:"Open Sans",Arial,sans-serif;color:var(--text);font-size:13px;line-height:1.6}
.page{position:relative;width:1200px;height:4956px}
.section{position:absolute;left:0;width:1200px}
.abs{position:absolute}
h2{font-family:"Open Sans",Arial,sans-serif;font-weight:400;color:var(--navy);font-size:27px;line-height:1.2}
.light h2,.light{color:var(--white)}
p{font-size:13px}
.btn-outline{display:inline-block;border:1px solid #b9c2cd;border-radius:20px;padding:6px 20px;font-size:11px;color:var(--ink);letter-spacing:.5px}
.media{position:absolute;border-radius:2px;overflow:hidden}
.play{position:absolute;left:50%;top:50%;width:58px;height:58px;margin:-29px 0 0 -29px;border-radius:50%;background:rgba(30,35,40,.75)}
.play::after{content:"";position:absolute;left:23px;top:17px;border-left:18px solid var(--white);border-top:12px solid transparent;border-bottom:12px solid transparent}

/* nav */
.topbar{top:0;height:72px;background:var(--white);border-bottom:1px solid var(--line)}
.brand{left:40px;top:22px;font-family:"Montserrat",Arial,sans-serif;font-weight:700;font-size:21px;letter-spacing:2px;color:var(--ink)}
.nav{right:40px;top:24px;display:flex;gap:22px;font-size:13px;color:var(--ink)}
.nav .active{color:var(--blue);border:1px solid var(--blue);padding:0 8px;margin-top:-1px}

/* hero */
.hero{top:72px;height:408px;background:linear-gradient(160deg,#2a5688 0%,#1b3f6a 45%,#16355c 100%)}
.hero-title{top:98px;width:100%;text-align:center;font-family:"Montserrat",Arial,sans-serif;font-weight:700;font-size:50px;letter-spacing:3px;color:var(--white)}
.hero-sub{top:168px;width:100%;text-align:center;font-size:24px;font-weight:600;color:var(--white)}
.hero-btn{top:228px;left:490px;width:220px;height:40px;border-radius:20px;background:var(--blue-soft);color:var(--white);font-size:12px;font-weight:600;letter-spacing:1px;text-align:center;line-height:40px}

/* angled bands */
.band{clip-path:polygon(0 0,50% 56px,100% 0,100% calc(100% - 56px),50% 100%,0 calc(100% - 56px))}

/* what we do */
.services{top:1020px;height:520px;background:linear-gradient(180deg,#2b2f33,#1e2226 60%,#2a2d31)}
.service{position:absolute;top:170px;width:230px;text-align:center;color:var(--white)}
.service .ring{width:86px;height:86px;margin:0 auto 20px;border:3px solid var(--white);border-radius:50%;display:flex;align-items:center;justify-content:center}
.service h3{font-weight:400;font-size:17px;margin-bottom:6px}
.service p{font-size:11px;color:#c9ced4;line-height:1.5}

/* feature lists */
.feature-grid{display:grid;grid-template-columns:1fr 1fr;gap:26px 30px}
.feature{display:flex;gap:12px;align-items:center}
.feature .icon{width:40px;height:40px;border:2px solid var(--blue);border-radius:50%;display:flex;align-items:center;justify-content:center;flex:none}
.feature h4{font-weight:600;font-size:15px;color:var(--ink);line-height:1.2}
.feature span{font-size:11px;color:var(--text)}

/* how it works */
.how{top:2020px;height:540px}
.how-panel{left:0;top:0;width:600px;height:540px;background:linear-gradient(180deg,#1d3f6b,#17345a);clip-path:polygon(0 0,100% 40px,100% 100%,0 calc(100% - 40px))}
.how-photo{left:600px;top:0;width:600px;height:540px;background:linear-gradient(180deg,#c9d6e3,#8fa6bd 55%,#2b3a4c);clip-path:polygon(0 40px,100% 0,100% calc(100% - 40px),0 100%)}
.step{position:absolute;left:100px;display:flex;gap:16px;width:420px}
.step .num{width:30px;height:30px;border-radius:50%;background:var(--blue-soft);color:var(--white);font-weight:700;text-align:center;line-height:30px;flex:none}
.step h4{color:var(--white);font-weight:400;font-size:16px;line-height:1.3}
.step p{color:#c3cfdd;font-size:11px;line-height:1.5}

/* expertise */
.expertise{top:3020px;height:420px;background:linear-gradient(180deg,#2e3236,#1d2125)}
.tile{position:absolute;top:250px;width:172px;height:70px;background:var(--white);border-radius:2px}
.tile::after{content:"";position:absolute;left:36px;top:29px;width:100px;height:12px;background:#c4cad2;border-radius:2px}

/* testimonials */
.testimonials{top:3940px;height:500px;background:linear-gradient(180deg,#4f82b7,#3d6fa5);clip-path:polygon(0 56px,50% 0,100% 56px,100% 100%,0 100%)}
.quote{position:absolute;top:185px;width:330px;display:flex;gap:14px}
.avatar{width:62px;height:62px;border-radius:50%;background:linear-gradient(180deg,#e7d9cc,#b79b86);border:3px solid var(--white);flex:none}
.quote p{font-size:11px;color:#e4ecf5;line-height:1.6}
.quote b{display:block;margin-top:10px;font-size:11px;color:var(--white);font-weight:600}
.quote small{font-size:10px;color:#cfdcea}
.dots{top:392px;left:0;width:100%;display:flex;justify-content:center;gap:8px}
.dots i{width:9px;height:9px;border-radius:50%;border:1px solid var(--white)}
.dots i:first-child{background:var(--white)}

/* contact */
.contact{top:4440px;height:516px}
.field{position:absolute;height:32px;border:1px solid var(--line);font-size:11px;color:#8a929c;padding:7px 10px;background:var(--white)}
.info-row{display:flex;gap:12px;align-items:center;margin-bottom:14px;font-size:11px;color:var(--ink)}
.info-row .icon{width:28px;height:28px;border:1px solid var(--line);border-radius:50%;display:flex;align-items:center;justify-content:center;flex:none}
.social{display:flex;gap:6px}
.social i{width:24px;height:24px;border-radius:50%;background:var(--navy)}
.social i:nth-child(2){background:var(--blue)}
.social i:nth-child(3){background:#b84a3c}
.social i:nth-child(4){background:#a06a3c}
.footer{top:4912px;width:100%;text-align:center;font-size:10px;color:#8a929c;border-top:1px solid var(--line);padding-top:14px}
</style>
</head>
<body>
<div class="page">

  <header class="section topbar">
    <div class="abs brand">FENWOLD STRATEGIES</div>
    <nav class="abs nav">
      <span class="active">Home</span><span>Who we are</span><span>What we Do</span><span>Core Capabilities</span><span>Industrial Expertise</span><span>Contact Us</span>
    </nav>
  </header>

  <section class="section hero" role="img" aria-label="Blue-toned photo of glass office towers viewed from below">
    <div class="abs hero-title">FENWOLD STRATEGIES</div>
    <div class="abs hero-sub">Full time recruiter and own a consulting firm</div>
    <div class="abs hero-btn">GET MORE INFO →</div>
    <svg class="abs" style="left:14px;top:190px" width="14" height="24" viewBox="0 0 14 24"><path d="M12 2 2 12l10 10" fill="none" stroke="#fff" stroke-width="2"/></svg>
    <svg class="abs" style="right:14px;top:190px" width="14" height="24" viewBox="0 0 14 24"><path d="M2 2l10 10-10 10" fill="none" stroke="#fff" stroke-width="2"/></svg>
    <svg class="abs" style="left:588px;top:366px" width="24" height="24" viewBox="0 0 24 24"><circle cx="12" cy="12" r="11" fill="rgba(255,255,255,.2)" stroke="#fff"/><path d="M7 10l5 5 5-5" fill="none" stroke="#fff" stroke-width="2"/></svg>
  </section>

  <section class="section" style="top:480px;height:540px">
    <h2 class="abs" style="left:100px;top:186px">Welcome to Fenwold Strategies</h2>
    <p class="abs" style="left:100px;top:232px;width:470px">We help growing firms find the right people and sharpen the way they plan, hire and lead, so every team can move with clarity and purpose.</p>
    <p class="abs" style="left:100px;top:290px;width:470px">Our practice blends hands-on recruiting with practical consulting, giving leaders a single partner for talent, structure and strategy. We listen first, then build simple plans that teams can carry forward long after our work is done.</p>
    <div class="abs btn-outline" style="left:100px;top:390px">READ MORE →</div>
    <div class="media" style="left:632px;top:188px;width:300px;height:168px;background:linear-gradient(135deg,#dfe6ee,#9fb3c8 60%,#5c6f86)" role="img" aria-label="Video still of a consultant presenting at a whiteboard to colleagues"><span class="play"></span></div>
  </section>

  <section class="section services band" role="img" aria-label="Dark photo of a laptop and desk, behind the services overview">
    <h2 class="abs" style="top:90px;width:100%;text-align:center;color:var(--white)">What We Do</h2>
    <div class="service" style="left:85px">
      <div class="ring"><svg width="40" height="34" viewBox="0 0 40 34"><rect x="3" y="2" width="34" height="22" fill="none" stroke="#fff" stroke-width="2.5"/><path d="M14 32h12M20 24v8" stroke="#fff" stroke-width="2.5"/></svg></div>
      <h3>Advanced Analytics</h3><p>Clear models that turn your data<br>into sound business decisions.</p>
    </div>
    <div class="service" style="left:355px">
      <div class="ring"><svg width="36" height="34" viewBox="0 0 36 34"><rect x="2" y="2" width="32" height="30" fill="none" stroke="#fff" stroke-width="2.5"/><path d="M10 26v-8M16 26V10M22 26v-12M28 26V14" stroke="#fff" stroke-width="3"/></svg></div>
      <h3>Corporate Finance</h3><p>Practical guidance on budgets,<br>capital and long range plans.</p>
    </div>
    <div class="service" style="left:625px">
      <div class="ring"><svg width="40" height="36" viewBox="0 0 40 36"><circle cx="14" cy="20" r="9" fill="none" stroke="#fff" stroke-width="5" stroke-dasharray="4 3"/><circle cx="14" cy="20" r="3" fill="#fff"/><circle cx="30" cy="9" r="6" fill="none" stroke="#fff" stroke-width="4" stroke-dasharray="3 2"/></svg></div>
      <h3>Performance Improvement</h3><p>Leaner processes that help teams<br>deliver more with less effort.</p>
    </div>
    <div class="service" style="left:880px">
      <div class="ring" style="background:#fff"><svg width="42" height="30" viewBox="0 0 42 30"><circle cx="21" cy="8" r="6" fill="#1e2226"/><path d="M10 28c0-8 22-8 22 0z" fill="#1e2226"/><circle cx="8" cy="12" r="4" fill="#1e2226"/><circle cx="34" cy="12" r="4" fill="#1e2226"/></svg></div>
      <h3>Customer Strategy</h3><p>Insight into the people you serve<br>and how best to reach them.</p>
    </div>
  </section>

  <section class="section" style="top:1540px;height:480px">
    <div class="media" style="left:100px;top:128px;width:340px;height:190px;background:linear-gradient(120deg,#e9edf2,#b8c6d4 55%,#7d8fa4)" role="img" aria-label="Video still of a businesswoman at a laptop in a bright office"><span class="play"></span></div>
    <h2 class="abs" style="left:600px;top:100px">Core Capabilities</h2>
    <p class="abs" style="left:600px;top:144px;width:470px">We bring a focused set of skills to every engagement, matched to the stage and needs of your business.</p>
    <div class="abs feature-grid" style="left:600px;top:210px;width:440px">
      <div class="feature"><span class="icon"><svg width="20" height="14" viewBox="0 0 20 14"><ellipse cx="10" cy="7" rx="9" ry="6" fill="none" stroke="#2f74b8" stroke-width="2"/><circle cx="10" cy="7" r="2.5" fill="#2f74b8"/></svg></span><div><h4>Visioning</h4><span>Set a clear direction</span></div></div>
      <div class="feature"><span class="icon"><svg width="16" height="18" viewBox="0 0 16 18"><rect x="1" y="1" width="14" height="16" fill="none" stroke="#2f74b8" stroke-width="2"/><path d="M4 6h8M4 10h8M4 14h5" stroke="#2f74b8" stroke-width="1.5"/></svg></span><div><h4>Assessment</h4><span>Know where you stand</span></div></div>
      <div class="feature"><span class="icon"><svg width="20" height="16" viewBox="0 0 20 16"><path d="M2 2h12v8H7l-4 4v-4H2z" fill="none" stroke="#2f74b8" stroke-width="2"/></svg></span><div><h4>Engagement</h4><span>Bring your team along</span></div></div>
      <div class="feature"><span class="icon"><svg width="20" height="16" viewBox="0 0 20 16"><path d="M2 8l5-5 3 3 3-3 5 5-8 7z" fill="none" stroke="#2f74b8" stroke-width="2"/></svg></span><div><h4>Partnership</h4><span>Work side by side</span></div></div>
    </div>
  </section>

  <section class="section how">
    <div class="abs how-panel"></div>
    <div class="abs how-photo" role="img" aria-label="Silhouettes of a business team meeting around a table by tall windows"></div>
    <h2 class="abs" style="left:100px;top:100px;color:var(--white)">How It Works</h2>
    <div class="step" style="top:160px"><span class="num">1</span><div><h4>Consulting</h4><p>We start with a frank talk about your goals, hiring needs and the gaps holding you back.</p></div></div>
    <div class="step" style="top:240px"><span class="num">2</span><div><h4>Process</h4><p>Together we map a plan with clear steps, owners and dates so progress is easy to track.</p></div></div>
    <div class="step" style="top:320px"><span class="num">3</span><div><h4>Solutions</h4><p>We place the right people and put the changes in motion, then check in until results hold.</p></div></div>
  </section>

  <section class="section" style="top:2560px;height:460px">
    <h2 class="abs" style="left:100px;top:120px">Who We Are</h2>
    <p class="abs" style="left:100px;top:164px;width:470px">Led by Marcus Fenwold, a full time recruiter with years of work in management consulting across many industries.</p>
    <p class="abs" style="left:100px;top:222px;width:470px">We are a small, hands-on team that values honest advice and lasting relationships. Clients choose us because we know both sides of the table: the people who do the work and the plans that guide it.</p>
    <div class="abs btn-outline" style="left:100px;top:320px">READ MORE →</div>
    <div class="media" style="left:632px;top:96px;width:368px;height:206px;background:linear-gradient(120deg,#dfe5ec,#a7b8ca 55%,#51657e)" role="img" aria-label="Video still of a consultant writing on a glass board while a colleague watches"><span class="play"></span></div>
  </section>

  <section class="section expertise band" role="img" aria-label="Dark photo of hands working over papers on a desk">
    <h2 class="abs" style="top:110px;width:100%;text-align:center;color:var(--white)">Industrial Expertise</h2>
    <p class="abs" style="top:156px;left:250px;width:700px;text-align:center;color:#c9ced4;font-size:11px">We have guided firms in technology, finance, health, retail and manufacturing, bringing lessons from each field to help clients hire well and grow with confidence.</p>
    <div class="tile" style="left:100px"></div>
    <div class="tile" style="left:307px"></div>
    <div class="tile" style="left:514px"></div>
    <div class="tile" style="left:721px"></div>
    <div class="tile" style="left:928px"></div>
  </section>

  <section class="section" style="top:3440px;height:500px">
    <div class="media" style="left:100px;top:140px;width:340px;height:206px;background:linear-gradient(120deg,#d6dde5,#9aabbd 55%,#5d6f83)" role="img" aria-label="Video still of hands pointing at documents during a meeting"><span class="play"></span></div>
    <h2 class="abs" style="left:600px;top:148px">Insights</h2>
    <p class="abs" style="left:600px;top:192px;width:470px">Short reads and videos on hiring, planning and growth, drawn from real client work.</p>
    <div class="abs feature-grid" style="left:600px;top:250px;width:440px">
      <div class="feature"><span class="icon"><svg width="18" height="16" viewBox="0 0 18 16"><rect x="1" y="4" width="16" height="11" fill="none" stroke="#2f74b8" stroke-width="2"/><path d="M6 4V1h6v3" fill="none" stroke="#2f74b8" stroke-width="2"/></svg></span><div><h4>Business Insights</h4><span>Notes for leaders</span></div></div>
      <div class="feature"><span class="icon"><svg width="18" height="16" viewBox="0 0 18 16"><path d="M1 15h16M3 15V7l4 3V5l4 3V1h4v14" fill="none" stroke="#2f74b8" stroke-width="2"/></svg></span><div><h4>Industry Insights</h4><span>Trends by sector</span></div></div>
      <div class="feature"><span class="icon"><svg width="16" height="18" viewBox="0 0 16 18"><circle cx="8" cy="7" r="6" fill="none" stroke="#2f74b8" stroke-width="2"/><path d="M5 16h6" stroke="#2f74b8" stroke-width="2"/></svg></span><div><h4>Capability Insights</h4><span>Skills that matter</span></div></div>
      <div class="feature"><span class="icon"><svg width="16" height="16" viewBox="0 0 16 16"><circle cx="8" cy="8" r="6" fill="none" stroke="#2f74b8" stroke-width="2"/><path d="M8 8V2A6 6 0 0 1 14 8z" fill="#2f74b8"/></svg></span><div><h4>Types</h4><span>Ways we engage</span></div></div>
    </div>
  </section>

  <section class="section testimonials">
    <h2 class="abs" style="top:110px;width:100%;text-align:center;color:var(--white)">Client Testimonials</h2>
    <div class="quote" style="left:100px"><span class="avatar" role="img" aria-label="Client portrait"></span><div><p>“Marcus found us three strong hires in a month and helped us rethink how the team is built.”</p><b>DANA WHITLEY</b><small>Operations Director</small></div></div>
    <div class="quote" style="left:440px"><span class="avatar" role="img" aria-label="Client portrait"></span><div><p>“Clear advice, quick follow through and a plan our managers actually used. We would work with him again.”</p><b>ROB KESSLER</b><small>Chief Executive</small></div></div>
    <div class="quote" style="left:780px"><span class="avatar" role="img" aria-label="Client portrait"></span><div><p>“He listened before he spoke and that made all the difference in how we planned our growth.”</p><b>ANN MORROW</b><small>Founder, Retail Group</small></div></div>
    <div class="abs dots"><i></i><i></i><i></i></div>
  </section>

  <section class="section contact">
    <h2 class="abs" style="top:50px;width:100%;text-align:center">Contact Us</h2>
    <div class="abs" style="left:100px;top:118px;font-weight:700;font-size:14px;color:var(--ink)">Get In Touch:</div>
    <div class="field" style="left:100px;top:150px;width:300px">Name</div>
    <div class="field" style="left:410px;top:150px;width:290px">Phone</div>
    <div class="field" style="left:100px;top:190px;width:300px">Email</div>
    <div class="field" style="left:410px;top:190px;width:290px">Company</div>
    <div class="field" style="left:100px;top:230px;width:600px;height:80px">Message</div>
    <div class="abs" style="left:630px;top:322px;width:70px;height:26px;border-radius:13px;background:var(--blue-soft);color:var(--white);font-size:10px;font-weight:600;text-align:center;line-height:26px">SUBMIT</div>
    <div class="abs" style="left:780px;top:118px;width:320px">
      <div style="font-weight:700;font-size:14px;color:var(--ink);margin-bottom:14px">Contact Information</div>
      <div class="info-row"><span class="icon"><svg width="10" height="14" viewBox="0 0 10 14"><path d="M5 13C1 8 1 6 1 5a4 4 0 0 1 8 0c0 1 0 3-4 8z" fill="#2f74b8"/></svg></span><span>400 Elm Avenue, Suite 210<br>Springfield, IL 62701</span></div>
      <div class="info-row"><span class="icon"><svg width="12" height="12" viewBox="0 0 12 12"><path d="M2 1l3 3-1.5 1.5a7 7 0 0 0 3 3L8 7l3 3-1.5 1.5C5 11 1 7 .5 2.5z" fill="#2f74b8"/></svg></span><span>555-0148</span></div>
      <div class="info-row"><span class="icon"><svg width="14" height="10" viewBox="0 0 14 10"><rect x="1" y="1" width="12" height="8" fill="none" stroke="#2f74b8" stroke-width="1.5"/><path d="M1 1l6 5 6-5" fill="none" stroke="#2f74b8" stroke-width="1.5"/></svg></span><span>info@marcusfenwold.net</span></div>
      <div class="social"><i></i><i></i><i></i><i></i></div>
    </div>
  </section>

  <footer class="abs footer">Copyright © 2017 Fenwold Strategies. All Rights Reserved.</footer>
</div>
</body>
</html>
```